Kesso Tea Premium Matcha brand Label

This is a label design project for a luxury tea brand. Feel free to be creative within the guidelines.
Attached to this project is a document called “Private Label Design Requirements” with the design guidelines and template. There is another document called "Kesso Tea Packaging Instructions" this has more details necessary to stick to the guidelines in the first document.

I have also attached the certifications to be included as well as different variations of the logo for you to use.

If you have any questions, I am here.
Updates

Need extra days to review

Target Market(s)

Young, active, fun, enjoy the finer things

```html
<!DOCTYPE html>
<html lang="en">
<head>
<meta charset="utf-8">
<title>Kesso Tea – Premium Organic Ceremonial Matcha Label</title>
<link rel="stylesheet" href="https://fonts.googleapis.com/css2?family=Raleway:wght@500;600;700;800&display=swap">
<style>
  :root {
    --stage-bg: #b7c6b2;
    --leaf-dark: #2f6b1e;
    --leaf-mid: #4f9a2c;
    --leaf-light: #86c64a;
    --panel-fill: rgba(255, 255, 255, 0.16);
    --panel-line: rgba(255, 255, 255, 0.75);
    --ink-white: #ffffff;
    --ink-lime: #d3e58a;
    --brand-green: #3e5a1c;
    --frame-green: #3d5d1f;
    --card-white: #ffffff;
    --badge-green: #1f7a3c;
    --badge-blue: #2f73b8;
  }
  * { box-sizing: border-box; margin: 0; padding: 0; }
  html, body {
    width: 1200px; height: 803px; overflow: hidden;
    background: var(--stage-bg);
    font-family: "Raleway", sans-serif;
  }
  .label {
    position: absolute; left: 51px; top: 294px;
    width: 1098px; height: 214px;
    overflow: hidden;
    box-shadow: 0 6px 12px rgba(0, 0, 0, 0.25);
  }
  .label__photo {
    position: absolute; inset: 0;
    background:
      radial-gradient(ellipse at 20% 40%, var(--leaf-light) 0%, transparent 45%),
      radial-gradient(ellipse at 75% 30%, var(--leaf-light) 0%, transparent 40%),
      radial-gradient(ellipse at 50% 90%, var(--leaf-dark) 0%, transparent 50%),
      linear-gradient(100deg, var(--leaf-mid), var(--leaf-dark) 45%, var(--leaf-mid) 70%, var(--leaf-dark));
  }
  .info-panel {
    position: absolute;
    border: 1.5px solid var(--panel-line);
    border-radius: 14px;
    background: var(--panel-fill);
    color: var(--ink-white);
    font-weight: 700;
    font-size: 10px;
    letter-spacing: -0.2px;
  }
  .info-panel--distributor {
    left: 79px; top: 113px; width: 228px; height: 54px;
    padding: 3px 0 0 16px; line-height: 15.5px;
    font-size: 9.5px; white-space: nowrap;
  }
  .info-panel--details {
    left: 778px; top: 43px; width: 246px; height: 131px;
    padding: 9px 0 0 14px;
    white-space: nowrap;
  }
  .details__heading {
    color: var(--ink-lime); font-size: 11.5px; font-weight: 600; line-height: 16px;
  }
  .details__text { padding-left: 9px; line-height: 17px; margin-bottom: 3px; }
  .details__steps { list-style: none; padding-left: 9px; line-height: 14px; }
  .details__steps li::before { content: "\2022\00a0"; }
  .brand-card {
    position: absolute; left: 461px; top: 18px; width: 176px; height: 179px;
    background: var(--card-white); padding: 19px;
  }
  .brand-card__frame {
    width: 100%; height: 100%;
    border: 2.5px solid var(--frame-green);
    display: flex; flex-direction: column; align-items: center;
    padding-top: 44px;
  }
  .brand-card__mark {
    width: 16px; height: 16px; border-radius: 50%;
    background: var(--brand-green); margin-bottom: 8px;
  }
  .brand-card__name {
    font-size: 15px; font-weight: 800; color: var(--brand-green); line-height: 18px;
  }
  .brand-card__product {
    margin-top: 6px; text-align: center;
    font-size: 10.5px; font-weight: 800; line-height: 14px; color: var(--brand-green);
  }
  .brand-card__weight {
    margin-top: 10px; font-size: 7px; font-weight: 700; color: #222;
  }
  .cert-badge { position: absolute; }
  .cert-badge--round {
    left: 698px; top: 137px; width: 32px; height: 32px; border-radius: 50%;
    background: var(--card-white); border: 3px solid var(--badge-green);
  }
  .cert-badge--square {
    left: 735px; top: 139px; width: 36px; height: 27px;
    background: var(--badge-blue); border: 2px solid var(--card-white);
  }
</style>
</head>
<body>
  <section class="label">
    <div class="label__photo" role="img" aria-label="Close-up photograph of fresh green tea leaves filling the label background"></div>

    <div class="info-panel info-panel--distributor">
      <p>Distributed by Kesso Tea Co. | Brookvale, Ga</p>
      <p>Certified Organic by ORVA</p>
      <p>PRODUCT OF JAPAN</p>
    </div>

    <div class="brand-card">
      <div class="brand-card__frame">
        <span class="brand-card__mark"></span>
        <p class="brand-card__name">Kesso Tea</p>
        <p class="brand-card__product">PREMIUM ORGANIC<br>CEREMONIAL MATCHA</p>
        <p class="brand-card__weight">Net Wt: 30g</p>
      </div>
    </div>

    <span class="cert-badge cert-badge--round" role="img" aria-label="Organic certification badge"></span>
    <span class="cert-badge cert-badge--square" role="img" aria-label="Non-GMO verification badge"></span>

    <div class="info-panel info-panel--details">
      <h2 class="details__heading">Ingredients</h2>
      <p class="details__text">Premium Organic Japanese Matcha Green Tea</p>
      <h2 class="details__heading">Instructions</h2>
      <ul class="details__steps">
        <li>2 tsp of Matcha</li>
        <li>2oz of Water (170-180 degrees F)</li>
        <li>Whisk in a W formation until frothy</li>
        <li>Sweeten to taste</li>
      </ul>
    </div>
  </section>
</body>
</html>
```